Car rental website design for a UAE car rental company

This project is about creating a new website design for a car rental company located in Dubai (United Arab Emirates), I opened the same project a few months ago but I didn't receive a lot of appealing entries so I closed it but this time I am marking the project as guaranteed to avoid such situation again, if you have already provided a design before then please re-submit again on this project so that it is considered while reviewing all the designs

A few important things:

1- We need a simple non-complex design
2- The final deliverable would be 2 screens (PSD, JPEG ... etc), the first screen is for the home page and the second screen is for an internal page
3- The home page must have a section that end users can use to rent a car online directly from the home page instead of going into some inner pages
4- The current website is very old and not very appealing so avoid creating a similar design (www.crestvane-autos.example)
5- The name is Crestvane but the company rents normal cars (no Limousin cars will be rented) so avoid adding any fancy cars in the images/graphics used in the design, just normal end users cars
6- The expected pages would be: home, About us, Our team, Strategy, Contact us and links to social media pages
7- The attachments include the company's logo and some screens from other car rental companies that provide online rentals/payments

If you have any questions please feel free to ask and please note that we will need the designs urgently

Thanks

Target Market(s)

Dubai - United Arab Emirates

Industry/Entity Type

It Company

Number of Pages Required

2 page

Font styles to use
Sans Serif

Requirements
Must have
• Check the project details
Nice to have
Should not have

```html
<!DOCTYPE html>
<html lang="en">
<head>
<meta charset="utf-8">
<title>Crestvane – Rent A Car</title>
<link rel="stylesheet" href="https://fonts.googleapis.com/css2?family=Oswald:wght@400;500;600&family=Arimo:wght@400;700&display=swap">
<style>
:root{
  --crimson:#9b0d3a;
  --crimson-dark:#6e0727;
  --slate:#7f8c86;
  --ink:#1c1c1c;
  --text:#333;
  --paper:#f7f7f7;
  --panel:#ececec;
  --field:#fff;
  --line:#d6d6d6;
  --footer:#111;
  --backdrop:#e4e4e4;
}
*{box-sizing:border-box;margin:0;padding:0}
html,body{width:1200px;height:927px;overflow:hidden;background:var(--backdrop)}
body{font-family:"Arimo",Arial,sans-serif;color:var(--text)}
.page{position:absolute;left:313px;top:0;width:557px;height:900px;background:var(--paper);transform:scale(1.03);transform-origin:0 0;box-shadow:0 0 12px rgba(0,0,0,.15)}
.page>*{position:absolute}

/* header */
.brand{left:44px;top:26px;display:flex;align-items:center;gap:8px}
.brand-square{width:22px;height:22px;background:var(--crimson)}
.brand-name{font-family:"Oswald",sans-serif;font-weight:500;font-size:18px;line-height:22px;color:var(--slate)}
.support{right:24px;top:28px;font-size:7px;font-weight:700;color:var(--ink);display:flex;align-items:center;gap:6px;letter-spacing:.2px}
.support b{font-size:9px}
.socials{display:flex;gap:10px}
.socials span{width:21px;height:21px;border-radius:50%;background:#333}
.socials--top{right:26px;top:50px}
.nav{left:0;top:81px;width:557px;height:23px;background:var(--crimson);display:flex;align-items:center;font-size:8px;color:#fff;text-transform:uppercase}
.nav a{color:#fff;text-decoration:none;text-align:center}
.nav .active{background:var(--crimson-dark);height:23px;line-height:23px;width:60px;margin-left:27px}

/* hero */
.hero-title{left:35px;top:132px;font-family:"Oswald",sans-serif;font-weight:600;font-size:30px;line-height:32px;color:var(--crimson);letter-spacing:-.3px;white-space:nowrap}
.hero-title span{color:var(--slate)}
.hero-lead{left:35px;top:171px;width:250px;font-size:8px;line-height:12px;color:var(--crimson)}
.hero-body{left:35px;top:199px;width:250px;font-size:6.3px;line-height:10.5px;color:var(--ink)}
.photo{background:radial-gradient(ellipse at 50% 55%,#b9bec3 0%,#d9dcdf 45%,var(--paper) 72%)}
.hero-car{left:88px;top:232px;width:190px;height:98px}
.btn{background:var(--crimson);color:#fff;font-family:"Oswald",sans-serif;font-size:6px;text-transform:uppercase;text-align:center;font-weight:500}
.hero-more{left:225px;top:320px;width:46px;height:12px;line-height:12px}

/* booking */
.booking{left:324px;top:120px;width:209px;height:221px;background:var(--panel)}
.booking>*{position:absolute;white-space:nowrap}
.tab{top:0;height:18px;line-height:18px;font-family:"Oswald",sans-serif;font-size:6.5px;text-align:center;color:#fff}
.tab--book{left:0;width:81px;background:var(--slate)}
.tab--manage{left:84px;width:125px;background:var(--crimson)}
.lbl{font-size:5.6px;line-height:7px;color:var(--crimson)}
.fld{background:var(--field);border:1px solid var(--line);height:11px;font-size:5.5px;line-height:9px;padding-left:4px;color:var(--ink)}
.spin{width:8px;height:11px;background:#222}
.cal{width:6px;height:6px;border:1px solid #555}
.days{right:12px;top:74px;font-size:7.5px;color:var(--crimson)}
.pick-title{left:9px;top:96px;font-size:7.5px;font-weight:700;color:var(--ink)}
.radio{width:6px;height:6px;border-radius:50%;border:1px solid #999;background:#fff}
.check{width:6px;height:6px;border:1px solid #999;background:#fff}
.quote{left:134px;top:196px;width:46px;height:14px;line-height:14px;font-size:6.5px}

/* sections */
.rule{left:26px;width:508px;height:1px;background:var(--line)}
.section-title{font-family:"Oswald",sans-serif;font-size:13px;line-height:16px}
.gallery-title{left:47px;top:358px;color:var(--crimson)}
.gallery-car{left:40px;top:388px;width:230px;height:92px}
.promo-head{left:315px;top:414px;font-family:"Oswald",sans-serif;font-size:14px;line-height:18px;font-weight:500;color:var(--ink);font-variant:small-caps;letter-spacing:.6px;white-space:nowrap}
.promo-head em{font-style:normal;color:var(--crimson);text-decoration:underline}
.promo-sub{left:295px;top:438px;font-family:"Oswald",sans-serif;font-size:11px;line-height:14px;color:var(--slate);white-space:nowrap}
.promo-more{left:356px;top:463px;width:94px;height:16px;line-height:16px;font-size:7px}
.mission-title{left:46px;top:528px;color:var(--ink)}
.mission-text{left:59px;top:553px;width:266px;font-size:6.5px;line-height:10.4px;color:var(--ink)}
.mission-photo{left:352px;top:554px;width:158px;height:102px;border:1px solid #999;background:linear-gradient(120deg,#6fd0cc 0%,#9fd8d4 22%,#b8b8b8 45%,#8a8a8a 100%)}
.mission-more{left:58px;top:643px;width:57px;height:16px;line-height:16px}
.service-title{left:50px;top:679px;color:var(--crimson)}
.service-intro{left:65px;top:702px;width:440px;font-size:8.4px;line-height:11px;font-weight:700;color:var(--ink)}
.services{font-size:6.2px;color:var(--ink);list-style:none}
.services li{display:flex;align-items:center;gap:6px;height:12.6px;white-space:nowrap}
.services svg{width:8px;height:8px;flex:none}
.services--left{left:68px;top:736px}
.services--right{left:304px;top:736px}
.sub{list-style:none;margin-left:24px;font-size:5.4px}
.sub li{height:9.8px;gap:4px}
.sub li::before{content:"–";font-weight:700}

/* footer */
.footer{left:0;top:844px;width:557px;height:27px;background:var(--footer);display:flex;align-items:center;font-family:"Oswald",sans-serif;font-size:6.5px;color:#fff}
.footer a{color:#fff;text-decoration:none}
.footer-links{display:flex;margin-left:47px}
.footer-links a{margin-right:27px}
.footer-mail{margin-left:auto;margin-right:25px;font-size:6.5px;white-space:nowrap}
.footer-mail span{font-size:9px;color:#aaa;margin-right:4px}
.copyright{left:79px;top:882px;font-size:7px;color:var(--ink)}
.socials--foot{right:24px;top:875px}
.socials--foot span{width:17px;height:17px;background:var(--crimson-dark)}
</style>
</head>
<body>
<main class="page">
  <div class="brand"><span class="brand-square"></span><span class="brand-name">Crestvane</span></div>
  <div class="support">PHONE SUPPORT
    <svg width="10" height="10" viewBox="0 0 24 24"><path d="M6.6 10.8a15 15 0 0 0 6.6 6.6l2.2-2.2c.3-.3.7-.4 1-.2 1.1.4 2.3.6 3.6.6.6 0 1 .4 1 1V20c0 .6-.4 1-1 1A17 17 0 0 1 3 4c0-.6.4-1 1-1h3.5c.6 0 1 .4 1 1 0 1.2.2 2.4.6 3.6.1.3 0 .7-.2 1z" fill="#9b0d3a"/></svg>
    <b>+971 4000 1280</b></div>
  <div class="socials socials--top"><span></span><span></span><span></span><span></span></div>

  <nav class="nav">
    <a class="active" href="#">Home</a>
    <a href="#" style="margin-left:29px">About us</a>
    <a href="#" style="margin-left:43px">Our team</a>
    <a href="#" style="margin-left:48px">Strategy</a>
    <a href="#" style="margin-left:46px">Contact us</a>
    <a href="#" style="margin-left:44px">Gallery</a>
  </nav>

  <h1 class="hero-title">Welcome To <span>Crestvane</span></h1>
  <p class="hero-lead">As Dubai is expected to welcome millions of tourists and visitors, car rental industry is believed to escalate more rapidly in the region.</p>
  <p class="hero-body">Over the past five years, demands for car rentals in Dubai has been augementing at a healthy pace and is currently registering a growth rate of 20 to 25 percent per year. The swift economic growth and the number...</p>
  <div class="photo hero-car" role="img" aria-label="Silver family sedan, front three-quarter view"></div>
  <div class="btn hero-more">Read more</div>

  <form class="booking">
    <div class="tab tab--book">Book a Car</div>
    <div class="tab tab--manage">View,modify or cancel a booking</div>

    <span class="lbl" style="left:9px;top:32px">Rental Start Date/Time</span>
    <div class="fld" style="left:78px;top:30px;width:60px">27 March 2015</div>
    <span class="cal" style="left:130px;top:33px"></span>
    <div class="fld" style="left:145px;top:30px;width:16px">10</div><span class="spin" style="left:160px;top:30px"></span>
    <div class="fld" style="left:176px;top:30px;width:20px">00</div><span class="spin" style="left:193px;top:30px"></span>

    <span class="lbl" style="left:9px;top:55px">Rental End Date/Time</span>
    <div class="fld" style="left:78px;top:53px;width:60px">29 March 2015</div>
    <span class="cal" style="left:130px;top:56px"></span>
    <div class="fld" style="left:145px;top:53px;width:16px">10</div><span class="spin" style="left:160px;top:53px"></span>
    <div class="fld" style="left:176px;top:53px;width:20px">00</div><span class="spin" style="left:193px;top:53px"></span>

    <span class="days">Number of Days 2</span>
    <span class="pick-title">Pick-up Location(City, State or Airport Code)</span>

    <span class="radio" style="left:13px;top:116px"></span><span class="lbl" style="left:24px;top:115px">Choose Station</span>
    <span class="radio" style="left:116px;top:116px"></span><span class="lbl" style="left:127px;top:115px">Choose Car Type</span>
    <span class="check" style="left:13px;top:130px"></span><span class="lbl" style="left:24px;top:129px">Returning to Same as pickup location</span>

    <span class="lbl" style="left:13px;top:144px">Pickup rental country</span>
    <div class="fld" style="left:82px;top:142px;width:93px">Dubai</div><span class="spin" style="left:174px;top:142px"></span>
    <span class="lbl" style="left:13px;top:160px">Rental location</span>
    <div class="fld" style="left:82px;top:158px;width:101px"></div>
    <span class="lbl" style="left:13px;top:177px">Sign Up your account</span>
    <div class="fld" style="left:82px;top:175px;width:93px">Select an account type</div><span class="spin" style="left:174px;top:175px"></span>

    <span class="check" style="left:13px;top:200px"></span><span class="lbl" style="left:24px;top:199px">Apply any discount Code</span>
    <div class="btn quote">Get Quote</div>
  </form>

  <div class="rule" style="top:349px"></div>
  <h2 class="section-title gallery-title">Gallary</h2>
  <div class="photo gallery-car" role="img" aria-label="Silver hatchback, side view"></div>
  <p class="promo-head">Experience an <em>extra</em> mile</p>
  <p class="promo-sub">of comfort, pleasure and leisure from the best</p>
  <div class="btn promo-more">Read more</div>

  <div class="rule" style="top:517px"></div>
  <h2 class="section-title mission-title">Mission &amp; Vision</h2>
  <div class="mission-text">
    <p>No sit feugiat consetetur volutpat et. Iriure magna ut at eirmod vero odio blandit sea gubergren lorem. Labore ea eu lorem sed labore feugait feugiat ullamcorper. Dolor no ut augue rebum sanctus esse illum sadipscing exerci. Sanctus placerat eirmod ut amet sit et et lorem.</p>
    <p>No sit feugiat consetetur volutpat et. Iriure magna ut at eirmod vero odio blandit sea gubergren lorem. Labore ea eu lorem sed labore feugait feugiat ullamcorper. Dolor no ut augue rebum sanctus esse illum sadipscing exerci. Sanctus placerat eirmod ut amet sit et et lorem.</p>
  </div>
  <div class="mission-photo" role="img" aria-label="Close-up of a hand holding a car key card"></div>
  <div class="btn mission-more">Read more</div>

  <div class="rule" style="top:674px"></div>
  <h2 class="section-title service-title">Service</h2>
  <p class="service-intro">Crestvane offers a comprehensive range of services including daily, short term and long term rental, chauffeur drive services for every purpose and budget.</p>

  <ul class="services services--left">
    <li><svg viewBox="0 0 10 10"><circle cx="5" cy="5" r="4.3" fill="none" stroke="#222"/><path d="M3 5.2l1.4 1.4L7.2 3.6" fill="none" stroke="#222" stroke-width="1.1"/></svg>Wide range of vehicles for city driving or SUV's for trips</li>
    <li><svg viewBox="0 0 10 10"><circle cx="5" cy="5" r="4.3" fill="none" stroke="#222"/><path d="M3 5.2l1.4 1.4L7.2 3.6" fill="none" stroke="#222" stroke-width="1.1"/></svg>Special 10% discount for new customers on the first rent</li>
    <li><svg viewBox="0 0 10 10"><circle cx="5" cy="5" r="4.3" fill="none" stroke="#222"/><path d="M3 5.2l1.4 1.4L7.2 3.6" fill="none" stroke="#222" stroke-width="1.1"/></svg>Long term car rental</li>
    <li style="height:auto;display:block">
      <ul class="sub">
        <li>New vehicles</li>
        <li>Fixed monthly expenditure</li>
        <li>Free registration and insurance</li>
        <li>Free maintenance and replacement vehicles</li>
        <li>No finance costs and no hidden costs</li>
      </ul>
    </li>
  </ul>
  <ul class="services services--right">
    <li><svg viewBox="0 0 10 10"><circle cx="5" cy="5" r="4.3" fill="none" stroke="#222"/><path d="M3 5.2l1.4 1.4L7.2 3.6" fill="none" stroke="#222" stroke-width="1.1"/></svg>sightseeing tours</li>
    <li><svg viewBox="0 0 10 10"><circle cx="5" cy="5" r="4.3" fill="none" stroke="#222"/><path d="M3 5.2l1.4 1.4L7.2 3.6" fill="none" stroke="#222" stroke-width="1.1"/></svg>Buyback option after lease term</li>
    <li><svg viewBox="0 0 10 10"><circle cx="5" cy="5" r="4.3" fill="none" stroke="#222"/><path d="M3 5.2l1.4 1.4L7.2 3.6" fill="none" stroke="#222" stroke-width="1.1"/></svg>Special offers for online bookings</li>
    <li><svg viewBox="0 0 10 10"><circle cx="5" cy="5" r="4.3" fill="none" stroke="#222"/><path d="M3 5.2l1.4 1.4L7.2 3.6" fill="none" stroke="#222" stroke-width="1.1"/></svg>airport transfers</li>
  </ul>

  <footer class="footer">
    <div class="footer-links">
      <a href="#">Home</a><a href="#">Our Team</a><a href="#">Strategy</a><a href="#">Gallary</a><a href="#">About Us</a><a href="#">Contact Us</a>
    </div>
    <div class="footer-mail"><span>Email Us :</span>hello@crestvane.example</div>
  </footer>
  <p class="copyright">@Copyright 2015, Crestvane. ALL RIGHTS RESERVED.</p>
  <div class="socials socials--foot"><span></span><span></span><span></span><span></span></div>
</main>
</body>
</html>
```